Complete redesign of Licensed Medical Cannabis Dispensary website

Redesign website to modernize it and simplify it and add a self service reservation/preorder interactive delivery form. Also integrate current POS system that has current inventory. Here is a website for inspiration that I really like because of it simplicity https://www.leafroute.example and easy ordering option. Attached is our logo.... please design around that and this is our website address www.meadowcrestcourier.example

Font styles to use
Sans Serif

Colors
5c5c5c
cbcbcb
000000
add136

Requirements
Must have
• inventory thats integrated with pos
• online reservation/delivery form
Nice to have
• a website thats modern and simple
• The website designed are the logo that is attached
Should not have
• too much information

```html
<!DOCTYPE html>
<html lang="en">
<head>
<meta charset="utf-8">
<title>Meadowcrest Courier — Medical Delivery</title>
<link href="https://fonts.googleapis.com/css2?family=Lora:ital,wght@0,400;0,700;1,400&family=Open+Sans:wght@400;600;700&display=swap" rel="stylesheet">
<style>
:root{
  --green:#add136;
  --grey:#5c5c5c;
  --grey-light:#cbcbcb;
  --black:#000000;
  --ink:#333333;
  --paper:#ffffff;
  --band:#f1f1f1;
  --dark:#3a3a3a;
}
*{box-sizing:border-box;margin:0;padding:0}
html,body{width:1200px;height:3472px;overflow:hidden}
body{font-family:"Open Sans",Arial,sans-serif;color:var(--ink);background:var(--paper)}
a{color:inherit;text-decoration:none}
.btn{display:inline-flex;align-items:center;justify-content:center;border-radius:22px;font-size:15px;font-weight:600;height:40px;padding:0 28px;color:#fff}
.btn-green{background:var(--green)}
.btn-dark{background:var(--dark)}

.topbar{height:36px;display:flex;align-items:center;justify-content:space-between;padding:0 90px;font-size:12px;color:var(--grey);border-bottom:1px solid #eee}
.topbar .phone{display:flex;align-items:center;gap:8px}
.topbar .tools{display:flex;gap:18px;align-items:center}

.header{height:116px;display:grid;grid-template-columns:1fr auto 1fr;align-items:center;padding:0 120px;font-size:14px;font-weight:600;color:var(--grey);letter-spacing:.5px}
.header .nav-left{display:flex;gap:40px;padding-left:10px}
.header .nav-right{display:flex;gap:40px;justify-content:flex-end;padding-right:30px}
.brand{display:flex;align-items:center;gap:12px;font-family:"Lora",Georgia,serif;font-weight:700;font-size:28px;color:var(--black)}
.brand .dot{width:22px;height:22px;border-radius:50%;background:var(--green)}

.hero{position:relative;height:470px;background:linear-gradient(120deg,#4a5640 0%,#2f3a2c 45%,#5d5f55 100%);color:#fff;text-align:center;overflow:hidden}
.hero .veil{position:absolute;inset:0;background:rgba(0,0,0,.35)}
.hero .content{position:relative;padding-top:100px}
.hero .kicker{font-family:"Lora",Georgia,serif;font-size:28px}
.hero h1{font-family:"Lora",Georgia,serif;font-weight:400;font-size:72px;letter-spacing:1px;line-height:1.15}
.hero p{font-size:15px;margin-top:8px}
.hero .actions{display:flex;gap:20px;justify-content:center;margin-top:24px}
.hero .curve{position:absolute;left:0;bottom:-1px;width:1200px;height:110px}

.doctor{text-align:center;height:200px;padding-top:40px}
.doctor h2{font-family:"Lora",Georgia,serif;font-weight:400;font-size:32px;line-height:1.3}
.doctor .btn{margin-top:22px;height:36px;font-size:14px}

.features{height:310px;display:flex;justify-content:center;gap:120px;text-align:center;padding-top:20px}
.feature{width:210px}
.feature .icon{width:108px;height:108px;border-radius:50%;margin:0 auto;display:flex;align-items:center;justify-content:center}
.feature .icon.green{background:var(--green)}
.feature .icon.grey{background:var(--grey)}
.feature h3{font-family:"Lora",Georgia,serif;font-weight:700;font-size:20px;margin-top:22px}
.feature p{font-size:12px;line-height:1.55;color:var(--grey);margin-top:8px}

.products{text-align:center}
.products.flowers{background:var(--band);height:500px;padding-top:44px}
.products.concentrate{background:var(--paper);height:540px;padding-top:60px}
.products h2{font-family:"Lora",Georgia,serif;font-weight:700;font-size:30px;letter-spacing:1px}
.grid{display:flex;gap:28px;justify-content:center;margin-top:30px}
.card{width:248px}
.card .photo{height:200px;display:flex;align-items:center;justify-content:center}
.card .photo .btn{height:30px;font-size:12px;padding:0 22px}
.card h4{font-family:"Lora",Georgia,serif;font-weight:700;font-size:20px;margin-top:20px;line-height:1.2}
.card .price{font-size:15px;color:var(--grey);margin-top:6px}
.dots{display:flex;gap:10px;justify-content:center}
.dots span{width:9px;height:9px;border-radius:50%;background:var(--grey-light)}
.dots span.on{background:var(--grey)}
.flowers .dots{margin-top:20px}
.concentrate .dots{margin-top:24px}

.reviews{position:relative;height:560px;background:linear-gradient(90deg,#2b2a26,#3f3b33 50%,#26251f);color:#fff;text-align:center;overflow:hidden}
.reviews .content{padding-top:80px}
.reviews h2{font-size:17px;font-weight:600;color:var(--green);letter-spacing:1px}
.quotes{display:flex;justify-content:center;gap:90px;margin-top:90px}
.quote{width:280px}
.quote .avatar{width:76px;height:76px;border-radius:50%;margin:0 auto;border:3px solid #fff}
.quote p{font-family:"Lora",Georgia,serif;font-style:italic;font-size:19px;line-height:1.45;color:var(--green);margin-top:44px}
.reviews .dots{position:absolute;left:0;right:0;bottom:40px}
.reviews .dots span{background:#777}
.reviews .dots span.on{background:#fff}

.member{height:140px;display:flex;align-items:center;justify-content:center;gap:120px}
.member h2{font-family:"Lora",Georgia,serif;font-weight:700;font-size:26px;letter-spacing:.5px}
.member .btn{height:38px;padding:0 34px}

.reserve{height:280px;background:var(--grey);color:#fff;text-align:center;padding-top:48px}
.reserve h2{font-family:"Lora",Georgia,serif;font-weight:700;font-size:26px;letter-spacing:1px}
.form{width:812px;margin:30px auto 0;display:grid;grid-template-columns:252px 260px 260px;gap:20px}
.field{height:38px;border-radius:19px;background:#fff;color:var(--ink);font-size:14px;font-weight:600;display:flex;align-items:center;padding:0 20px;justify-content:space-between}
.field.wide{grid-column:span 2}
.form .btn{height:38px;border-radius:19px}

.footer{height:276px;background:var(--band);display:grid;grid-template-columns:288px 312px 232px 1fr;padding:40px 0 0 80px;font-size:13px;color:var(--grey)}
.footer h5{font-size:14px;font-weight:700;color:var(--ink);letter-spacing:.5px;margin-bottom:16px}
.footer li{list-style:none;margin-bottom:8px;display:flex;gap:8px;align-items:center}
.footer li::before{content:"";border-left:5px solid var(--grey);border-top:4px solid transparent;border-bottom:4px solid transparent}
.newsletter .input{width:200px;height:36px;border-radius:18px;background:#fff;border:1px solid var(--grey-light);display:flex;align-items:center;padding:0 16px;color:var(--ink)}
.newsletter .btn{margin-top:14px;height:34px;font-size:13px;padding:0 24px}
.bottom{height:44px;background:#e2e2e2;display:flex;align-items:center;justify-content:space-between;padding:0 40px;font-size:12px;color:var(--grey)}
</style>
</head>
<body>

<div class="topbar">
  <div class="phone">
    <svg width="14" height="14" viewBox="0 0 24 24"><path d="M6.6 10.8a15 15 0 006.6 6.6l2.2-2.2a1 1 0 011-.2 11 11 0 003.6.6 1 1 0 011 1V20a1 1 0 01-1 1A17 17 0 013 4a1 1 0 011-1h3.5a1 1 0 011 1 11 11 0 00.6 3.6 1 1 0 01-.3 1z" fill="#5c5c5c"/></svg>
    (800) 555-0142
  </div>
  <div class="tools">
    <svg width="16" height="16" viewBox="0 0 24 24"><path d="M3 4h3l2.5 11h10L21 7H7" fill="none" stroke="#5c5c5c" stroke-width="2"/><circle cx="10" cy="19" r="1.6" fill="#5c5c5c"/><circle cx="17" cy="19" r="1.6" fill="#5c5c5c"/></svg>
    <svg width="14" height="14" viewBox="0 0 24 24"><circle cx="12" cy="8" r="4" fill="#5c5c5c"/><path d="M4 21c1-5 15-5 16 0z" fill="#5c5c5c"/></svg>
  </div>
</div>

<header class="header">
  <nav class="nav-left"><a>LOGIN/SIGN UP</a><a>CONTACT</a></nav>
  <div class="brand"><span class="dot"></span>Meadowcrest Courier</div>
  <nav class="nav-right"><a>FORUMS</a><a>STORE</a></nav>
</header>

<section class="hero" role="img" aria-label="Cannabis plant close-up with a patient in the background">
  <div class="veil"></div>
  <div class="content">
    <div class="kicker">Top Sell Medical</div>
    <h1>Marijuana Delivery</h1>
    <p>We Offer Only the Highest quality flowers, edibles and Concentrates</p>
    <div class="actions"><a class="btn btn-green">Shop Now</a><a class="btn btn-dark">Get Verified</a></div>
  </div>
  <svg class="curve" viewBox="0 0 1200 110" preserveAspectRatio="none"><path d="M0 30 Q600 150 1200 30 L1200 110 L0 110 Z" fill="#ffffff"/></svg>
</section>

<section class="doctor">
  <h2>Don't have your doctor's recommendation yet? Get it<br>online for just $49!</h2>
  <a class="btn btn-green">Get Started</a>
</section>

<section class="features">
  <div class="feature">
    <div class="icon green"><svg width="44" height="52" viewBox="0 0 44 52"><path d="M4 2h26l10 10v38H4z" fill="#fff"/><path d="M13 28l7 7 12-13" fill="none" stroke="#add136" stroke-width="4"/></svg></div>
    <h3>Get Verified</h3>
    <p>It's fast, it's simple. Just fill out our verification form and get approved in minutes.</p>
  </div>
  <div class="feature">
    <div class="icon grey"><svg width="50" height="44" viewBox="0 0 50 44"><path d="M2 14h46l-6 28H8z" fill="#fff"/><path d="M14 14L22 2M36 14L28 2" stroke="#fff" stroke-width="3"/><path d="M18 22v12M25 22v12M32 22v12" stroke="#5c5c5c" stroke-width="3"/></svg></div>
    <h3>Shop</h3>
    <p>Add the products you want to your shopping cart and check out. No credit card required!</p>
  </div>
  <div class="feature">
    <div class="icon green"><svg width="50" height="46" viewBox="0 0 50 46"><path d="M25 2l22 10v22L25 44 3 34V12z" fill="#fff"/><path d="M3 12l22 10 22-10M25 22v22" fill="none" stroke="#add136" stroke-width="3"/></svg></div>
    <h3>Get Medicated</h3>
    <p>Sit back and relax. Our professional staff will deliver your medication right to your front door.</p>
  </div>
</section>

<section class="products flowers">
  <h2>FLOWERS</h2>
  <div class="grid">
    <div class="card"><div class="photo" role="img" aria-label="Flower bud close-up" style="background:linear-gradient(135deg,#6f7a4a,#3e4a2a)"><a class="btn btn-green">Buy Now</a></div><h4>Velvet Glue</h4><div class="price">$30.00</div></div>
    <div class="card"><div class="photo" role="img" aria-label="Flower buds close-up" style="background:linear-gradient(135deg,#8a8a62,#4d5036)"><a class="btn btn-dark">Buy Now</a></div><h4>Sugarfield</h4><div class="price">$15.00 – $30.00</div></div>
    <div class="card"><div class="photo" role="img" aria-label="Flower buds close-up" style="background:linear-gradient(135deg,#7c8555,#454d2c)"><a class="btn btn-dark">Buy Now</a></div><h4>Ridgeback Glue</h4><div class="price">$35.00</div></div>
    <div class="card"><div class="photo" role="img" aria-label="Flower buds close-up" style="background:linear-gradient(135deg,#6a7248,#3a4128)"><a class="btn btn-dark">Buy Now</a></div><h4>Azure Biscuits<br>(Private Reserve)</h4><div class="price">$30.00</div></div>
  </div>
  <div class="dots"><span></span><span class="on"></span><span></span><span></span></div>
</section>

<section class="products concentrate">
  <h2>CONCENTRATE</h2>
  <div class="grid">
    <div class="card"><div class="photo" role="img" aria-label="Live resin jar" style="background:linear-gradient(135deg,#5f5a45,#2f2d24)"><a class="btn btn-green">Buy Now</a></div><h4>Harbor White Live<br>Resin</h4><div class="price">$30.00</div></div>
    <div class="card"><div class="photo" role="img" aria-label="Budder concentrate jar" style="background:linear-gradient(135deg,#b08a3c,#5a4420)"><a class="btn btn-dark">Buy Now</a></div><h4>Harbor's Budder</h4><div class="price">$40.00</div></div>
    <div class="card"><div class="photo" role="img" aria-label="Vape cartridges" style="background:linear-gradient(135deg,#3a3a36,#1c1c1a)"><a class="btn btn-dark">Buy Now</a></div><h4>Zestberry Cart.</h4><div class="price">$30.00</div></div>
    <div class="card"><div class="photo" role="img" aria-label="Vape cartridge on leaves" style="background:linear-gradient(135deg,#4f5a3a,#262b1c)"><a class="btn btn-dark">Buy Now</a></div><h4>RG#7 CART</h4><div class="price">$30.00</div></div>
  </div>
  <div class="dots"><span></span><span class="on"></span><span></span><span></span></div>
</section>

<section class="reviews" role="img" aria-label="Hands rolling cannabis on a wooden table">
  <div class="content">
    <h2>WHAT OUR CUSTOMERS SAY ABOUT OUR DISPENSARY...</h2>
    <div class="quotes">
      <div class="quote"><div class="avatar" role="img" aria-label="Customer portrait" style="background:#a8876e"></div><p>"This dispensary has the very best med! I love their new place!"</p></div>
      <div class="quote"><div class="avatar" role="img" aria-label="Customer portrait" style="background:#6b5a48"></div><p>"These guys really know their stuff man. Nothin' but the kind here!"</p></div>
    </div>
  </div>
  <div class="dots"><span></span><span class="on"></span><span></span><span></span></div>
</section>

<section class="member">
  <h2>STILL NOT A MEMBER OF OUR DISPENSARY?</h2>
  <a class="btn btn-green">Get Verified Now</a>
</section>

<section class="reserve">
  <h2>RESERVATION</h2>
  <div class="form">
    <div class="field">Name</div>
    <div class="field">Email</div>
    <div class="field">Phone</div>
    <div class="field wide">Select a Product<svg width="12" height="8" viewBox="0 0 12 8"><path d="M1 1l5 5 5-5" fill="none" stroke="#5c5c5c" stroke-width="2"/></svg></div>
    <a class="btn btn-green">Book Now</a>
  </div>
</section>

<footer class="footer">
  <div><h5>EXPLORE</h5><ul><li>Home</li><li>Cart</li><li>My Account</li><li>New Patient Verification</li><li>Contact Us</li></ul></div>
  <div><h5>FORUMS</h5><ul><li>Bongs, Bubblers, &amp; Water Pipes</li><li>Concentrates</li><li>Growing</li><li>Vaporizers</li><li>What Are You Smokin'?</li></ul></div>
  <div><h5>RECENT TOPICS</h5><ul><li>Glass or wood?</li><li>Saving your plants</li></ul></div>
  <div class="newsletter"><h5>Newsletter</h5><div class="input">Enter email id</div><a class="btn btn-green">Subscribe Now</a></div>
</footer>
<div class="bottom"><span>© 2018, Company Name – All Right Reserved</span><span>Top ▲</span></div>

</body>
</html>
```